FunBrixo Business Card

We need a business card design for our company. We sell construction-themed amusement rides for kids.

Contact Information for Business Card

Contact info on business card should include:
Carl Dunning
Co-Founder & COO
(833) 571-FUNBRIX
Carl@funbrixo-demo.com
www.funbrixo-demo.com

```html
<!DOCTYPE html>
<html lang="en">
<head>
<meta charset="UTF-8">
<title>FunBrixo Business Card</title>
<link rel="stylesheet" href="https://fonts.googleapis.com/css2?family=Poppins:wght@400;500;700;800&display=swap">
<style>
  :root {
    --bg: #8f8f8f;
    --card-dark: #1f1f21;
    --card-light: #ffffff;
    --orange: #e8632a;
    --blue: #1fa3de;
    --pink: #e6177f;
    --purple: #8e2a92;
    --yellow: #f4a423;
    --ink: #3b3b3b;
    --faint-a: #f3e9d6;
    --faint-b: #eef0f3;
  }
  * { box-sizing: border-box; margin: 0; padding: 0; }
  html, body { width: 1200px; height: 960px; overflow: hidden; }
  body {
    background: var(--bg);
    font-family: "Poppins", sans-serif;
    position: relative;
  }
  .card {
    position: absolute;
    width: 700px;
    height: 400px;
    border-radius: 22px;
    overflow: hidden;
    box-shadow: 0 10px 24px rgba(0,0,0,0.25);
  }
  /* Front */
  .card-front {
    left: 250px; top: 50px;
    background: var(--card-dark);
    display: flex;
    align-items: center;
    justify-content: center;
    gap: 22px;
  }
  .brand-dot {
    width: 44px; height: 44px;
    border-radius: 50%;
    background: var(--orange);
  }
  .brand-name-large {
    font-weight: 800;
    font-size: 88px;
    color: var(--orange);
    letter-spacing: -1px;
  }
  /* Back */
  .card-back {
    left: 250px; top: 500px;
    background: var(--card-light);
  }
  .character-art {
    position: absolute;
    left: 70px; top: 70px;
    width: 340px; height: 330px;
    background: linear-gradient(160deg, var(--faint-a) 0%, var(--faint-b) 70%);
    opacity: 0.8;
    border-radius: 40px 40px 0 0;
  }
  .brand-name-small {
    position: absolute;
    right: 60px; top: 36px;
    font-weight: 800;
    font-size: 34px;
    color: var(--orange);
  }
  .divider {
    position: absolute;
    left: 0; right: 0;
    top: 196px;
    height: 1.5px;
    background: var(--orange);
  }
  .contact-block {
    position: absolute;
    left: 34px; top: 228px;
    width: 300px;
  }
  .person-name {
    font-weight: 700;
    font-size: 22px;
    color: var(--orange);
    text-transform: uppercase;
    line-height: 1.1;
  }
  .person-title {
    font-weight: 400;
    font-size: 15px;
    color: var(--blue);
    margin-top: 2px;
  }
  .contact-rule {
    height: 1px;
    background: var(--orange);
    margin: 10px 0 10px;
    width: 260px;
  }
  .contact-list { list-style: none; }
  .contact-list li {
    display: flex;
    align-items: center;
    gap: 10px;
    font-size: 14px;
    color: var(--ink);
    line-height: 1.6;
  }
  .contact-list svg { width: 13px; height: 13px; flex: none; }
  .edge-band {
    position: absolute;
    left: 0; right: 0; bottom: 0;
    height: 12px;
    display: flex;
  }
  .edge-band span { display: block; height: 100%; }
  .band-orange { flex: 7; background: var(--orange); }
  .band-blue { flex: 0.75; background: var(--blue); }
  .band-pink { flex: 0.75; background: var(--pink); }
  .band-purple { flex: 0.75; background: var(--purple); }
  .band-yellow { flex: 0.75; background: var(--yellow); }
</style>
</head>
<body>
  <section class="card card-front" aria-label="Business card front">
    <span class="brand-dot"></span>
    <span class="brand-name-large">FunBrixo</span>
  </section>

  <section class="card card-back" aria-label="Business card back">
    <div class="character-art" role="img" aria-label="Faint illustration of two cartoon construction workers in hard hats"></div>
    <div class="brand-name-small">FunBrixo</div>
    <div class="divider"></div>

    <div class="contact-block">
      <p class="person-name">Carl Dunning</p>
      <p class="person-title">Co-Founder &amp; COO</p>
      <div class="contact-rule"></div>
      <ul class="contact-list">
        <li>
          <svg viewBox="0 0 16 16" aria-hidden="true"><path fill="#e8632a" d="M3.6 1.2l2.2 2.6-1.3 1.6c.9 2 2.3 3.4 4.3 4.3l1.6-1.3 2.6 2.2-1.4 2.4C6.6 12.7 3.3 9.4 1.2 4.4z"/></svg>
          (833) 571-FUNBRIX
        </li>
        <li>
          <svg viewBox="0 0 16 16" aria-hidden="true"><rect x="1" y="3" width="14" height="10" rx="1.5" fill="#e8632a"/><path d="M1.5 4l6.5 5 6.5-5" fill="none" stroke="#fff" stroke-width="1.3"/></svg>
          Carl@funbrixo-demo.com
        </li>
        <li>
          <svg viewBox="0 0 16 16" aria-hidden="true"><circle cx="8" cy="8" r="7" fill="#e8632a"/><path d="M1.5 8h13M8 1c-3 3.5-3 10.5 0 14M8 1c3 3.5 3 10.5 0 14" fill="none" stroke="#fff" stroke-width="1"/></svg>
          www.funbrixo-demo.com
        </li>
      </ul>
    </div>

    <div class="edge-band" aria-hidden="true">
      <span class="band-orange"></span>
      <span class="band-blue"></span>
      <span class="band-pink"></span>
      <span class="band-purple"></span>
      <span class="band-yellow"></span>
    </div>
  </section>
</body>
</html>
```